We are a specialised Chartered Accountant recruiting business and we are hosting a Casino Night for newly qualified CAs.1. We need a flyer Designed that will be sent out to all newly qualified CAs with 1. Information about the event and to 2. probe them to attendThe below information to be included:Date : 07th of November 2019 (Thursday)Venue : Copper Lantern Grill Johannesburg | Peltoni Vaal Plaza, 14 Orrin Lane, SandtonArrive : 18: 30 Dress code : Smart Casual / CocktailEntertainment : Drinks & Snacks will be provided RSVP : Movent Representative
Target Market(s)
23 - 27 year olds
Colors
Designer to choose colors to be used in the design.
Requirements
Must have
- The Flyer must have the event Title " Quillfern Staffing Movent Casino Night
- Must have the below details
- Date : 07th of November 2019 (Thursday)
- Venue : Copper Lantern Grill Johannesburg | Peltoni Vaal Plaza, 14 Orrin Lane,
- Sandton
- Arrive : 18: 30
- Dress code : Smart Casual / Cocktail
- Entertainment : Drinks & Snacks will be provided
- RSVP : Movent Representative
Nice to have
- Can use either one of the images we sent through not necessarily both
Should not have
- Must have all the details i have provided about the event.
- Must have a catchy line inviting people to come to the event.

```html
<!DOCTYPE html>
<html lang="en">
<head>
<meta charset="utf-8">
<title>Quillfern Staffing Movent Casino Night</title>
<link rel="stylesheet" href="https://fonts.googleapis.com/css2?family=Bebas+Neue&family=Great+Vibes&family=Open+Sans:wght@400;600&display=swap">
<style>
  :root {
    --page: #e6e4e1;
    --ink: #0b0b0c;
    --ink-soft: #17171a;
    --gold: #e7b93c;
    --gold-light: #fbe7a1;
    --gold-deep: #b8862a;
    --amber: #f2a51f;
    --silver: #d9d9db;
    --silver-dark: #8c8c90;
    --white: #ffffff;
    --red: #c4161c;
  }
  * { margin: 0; padding: 0; box-sizing: border-box; }
  html, body { width: 996px; height: 1200px; overflow: hidden; background: var(--page); }
  .flyer {
    position: absolute; left: 51px; top: 20px; width: 894px; height: 1160px;
    background: linear-gradient(180deg, var(--ink) 0%, var(--ink) 48%, var(--ink-soft) 52%, var(--ink) 100%);
    overflow: hidden; color: var(--white);
    font-family: "Open Sans", Arial, sans-serif;
  }
  .flyer__lines { position: absolute; inset: 0; }
  .hero-art {
    position: absolute; left: 0; top: 0; width: 894px; height: 430px;
    background:
      radial-gradient(ellipse 260px 170px at 460px 300px, var(--silver) 0%, var(--silver-dark) 45%, rgba(40,40,42,0) 80%),
      radial-gradient(ellipse 480px 200px at 447px 90px, rgba(196,22,28,0.75) 0%, rgba(90,10,14,0.4) 55%, rgba(0,0,0,0) 85%);
  }
  .title { position: absolute; left: 0; width: 100%; text-align: center; }
  .title__host {
    top: 432px; font-family: "Bebas Neue", Impact, sans-serif; font-size: 46px; line-height: 46px;
    color: var(--white); letter-spacing: 0.5px;
  }
  .title__main {
    top: 462px; font-family: "Bebas Neue", Impact, sans-serif; font-size: 194px; line-height: 194px;
    letter-spacing: -2px;
    background: linear-gradient(180deg, #f4f4f5 0%, var(--silver) 45%, #6d6d72 50%, var(--silver) 80%, #a9a9ad 100%);
    -webkit-background-clip: text; background-clip: text; color: transparent;
  }
  .title__script {
    top: 596px; font-family: "Great Vibes", cursive; font-size: 96px; line-height: 100px; color: var(--white);
  }
  .details { position: absolute; left: 0; width: 100%; text-align: center; }
  .details__date {
    top: 776px; font-family: "Bebas Neue", Impact, sans-serif; font-size: 38px; line-height: 40px; color: var(--amber);
  }
  .rule { position: absolute; left: 203px; width: 494px; height: 1px; background: var(--gold); }
  .rule--top { top: 824px; }
  .rule--bottom { top: 907px; }
  .details__venue { top: 840px; font-size: 19px; line-height: 26px; color: var(--white); }
  .details__extras { top: 929px; font-size: 19px; line-height: 26px; color: var(--amber); }
  .rsvp {
    position: absolute; left: 232px; top: 1000px; width: 396px; height: 47px; border-radius: 14px;
    background: linear-gradient(90deg, var(--gold-deep) 0%, var(--gold) 30%, var(--gold-light) 70%, var(--gold) 100%);
    font-family: "Bebas Neue", Impact, sans-serif; font-size: 27px; line-height: 49px;
    text-align: center; color: var(--ink);
  }
</style>
</head>
<body>
  <main class="flyer">
    <div class="hero-art" role="img" aria-label="Playing cards of aces, casino chips, red dice and scattered red hearts and dark suit symbols"></div>

    <svg class="flyer__lines" width="894" height="1160" viewBox="0 0 894 1160" aria-hidden="true">
      <defs>
        <linearGradient id="goldStroke" x1="0" y1="0" x2="1" y2="1">
          <stop offset="0" stop-color="#b8862a"/>
          <stop offset="0.5" stop-color="#fbe7a1"/>
          <stop offset="1" stop-color="#e7b93c"/>
        </linearGradient>
      </defs>
      <g fill="none" stroke="#e7b93c" stroke-width="1">
        <line x1="0" y1="390" x2="430" y2="2"/>
        <line x1="464" y1="2" x2="894" y2="390"/>
        <line x1="0" y1="765" x2="330" y2="1160"/>
        <line x1="894" y1="765" x2="564" y2="1160"/>
        <polyline points="20,20 120,20 120,120"/>
        <polyline points="874,20 774,20 774,120"/>
        <polyline points="20,1140 120,1140 120,1040"/>
        <polyline points="874,1140 774,1140 774,1040"/>
        <rect x="93" y="82" width="712" height="992"/>
      </g>
      <rect x="69" y="66" width="759" height="1029" fill="none" stroke="url(#goldStroke)" stroke-width="4"/>
      <g fill="#e7b93c">
        <circle cx="28" cy="22" r="8"/><circle cx="44" cy="40" r="4"/><circle cx="54" cy="50" r="2.5"/>
        <circle cx="866" cy="22" r="8"/><circle cx="850" cy="40" r="4"/><circle cx="840" cy="50" r="2.5"/>
        <circle cx="28" cy="1138" r="8"/><circle cx="44" cy="1120" r="4"/><circle cx="54" cy="1110" r="2.5"/>
        <circle cx="866" cy="1138" r="8"/><circle cx="850" cy="1120" r="4"/><circle cx="840" cy="1110" r="2.5"/>
      </g>
    </svg>

    <h1>
      <span class="title title__host">Quillfern Staffing Movent</span>
      <span class="title title__main">CASINO</span>
      <span class="title title__script">Night</span>
    </h1>

    <p class="details details__date">THURSDAY 07TH, NOVEMBER 2019</p>
    <div class="rule rule--top"></div>
    <p class="details details__venue">Venue : Copper Lantern Grill Johannesburg<br>Peltoni Vaal Plaza, 14 Orrin Lane, SandtonArrive : 18: 30</p>
    <div class="rule rule--bottom"></div>
    <p class="details details__extras">Dress code : Smart Casual / CocktailEntertainment<br>Drinks &amp; Snacks will be provided</p>
    <div class="rsvp">RSVP : MOVENT REPRESENTATIVE</div>
  </main>
</body>
</html>
```